Fun, Clean Business Card For Family Focused Travel Agency

I need a business card using specific colors and fonts as in the uploaded files. Ideally, I would like a large image of the logo on the back and all the contact info on the front. Maybe the stars/dots somewhere in a flowy form.

I do want it the contact information to be clear and easy to read. I don't want it to look too busy. Maybe even a bit minimalist.

I plan or ordering the ROUNDED CORNER business cards from Cardwell Press, so please consider that in your design.

Target Market(s)

Families with children, couples, groups of friends

Contact Information for Business Card

Marla Quint, Owner
Marla@TumbleTrips.example
Cell Phone Number 555-218-4603
Office Phone Number 555-647-1925
Specializing in Glimmerland destinations, Pelican Bay Fun Park, Cruises and All-Inclusive Vacations.

Nice but not required:
www.TumbleTrips.example
Facebook, Instagram, Twitter icons with username: TumbleTrips

Font styles to use
Sans Serif

Requirements
Must have
• Please try to use the colors from the logo as much as possible. I understand lighter shades/colors may be needed for some things.
Should not have
• NO SERIF FONTS. That is really the only thing I do not want at all

```html
<!DOCTYPE html>
<html lang="en">
<head>
<meta charset="utf-8">
<title>TumbleTrips Business Card</title>
<link href="https://fonts.googleapis.com/css2?family=Kaushan+Script&family=Open+Sans:wght@400&family=Roboto+Condensed:wght@400;700&display=swap" rel="stylesheet">
<style>
  :root {
    --backdrop: #dcd7d7;
    --card-white: #fbfbfb;
    --ink: #1b2230;
    --teal: #17a88a;
    --teal-bright: #07b594;
    --deep: #1a2830;
    --blue: #3a8fd0;
    --green: #8cbf3f;
    --yellow: #e9b730;
    --orange: #e2702a;
  }
  * { margin: 0; padding: 0; box-sizing: border-box; }
  html, body { width: 1200px; height: 1176px; overflow: hidden; }
  body {
    background: var(--backdrop);
    position: relative;
    font-family: "Roboto Condensed", "Arial Narrow", sans-serif;
  }
  .card {
    position: absolute;
    left: 247px;
    width: 688px;
    border-radius: 22px;
    overflow: hidden;
  }
  .card-front {
    top: 147px;
    height: 395px;
    background: linear-gradient(160deg, #ffffff 0%, var(--card-white) 60%, #f1f1f1 100%);
  }
  .card-back {
    top: 595px;
    height: 393px;
    background: linear-gradient(180deg, var(--teal-bright) 0%, #0f8f78 30%, #1d5a54 65%, var(--deep) 100%);
  }
  .holder-name {
    position: absolute;
    top: 150px;
    left: 0;
    width: 100%;
    text-align: center;
    font-family: "Kaushan Script", cursive;
    font-size: 40px;
    color: var(--ink);
    line-height: 1;
  }
  .holder-title {
    position: absolute;
    top: 205px;
    left: 0;
    width: 100%;
    text-align: center;
    font-family: "Open Sans", sans-serif;
    font-size: 21px;
    color: var(--teal);
    letter-spacing: 0.5px;
  }
  .contact-row {
    position: absolute;
    top: 297px;
    left: 22px;
    right: 22px;
    display: flex;
    justify-content: space-between;
    align-items: center;
    font-size: 14.5px;
    color: var(--ink);
  }
  .contact-item { display: flex; align-items: center; gap: 6px; white-space: nowrap; }
  .contact-item svg { width: 15px; height: 15px; fill: none; stroke: var(--teal); stroke-width: 1.6; }
  .contact-item svg .solid { fill: var(--teal); stroke: none; }
  .rule {
    position: absolute;
    top: 327px;
    left: 23px;
    right: 25px;
    height: 2px;
    background: linear-gradient(90deg, var(--blue) 0%, var(--teal) 30%, var(--green) 50%, var(--yellow) 75%, var(--orange) 100%);
  }
  .specialties {
    position: absolute;
    top: 354px;
    left: 0;
    width: 100%;
    display: flex;
    justify-content: center;
    gap: 10px;
    font-size: 15px;
    color: var(--ink);
  }
  .specialty { display: flex; align-items: center; gap: 3px; }
  .specialty svg { width: 11px; height: 11px; }
  .brand {
    position: absolute;
    top: 0; left: 0; width: 100%; height: 100%;
    display: flex;
    align-items: center;
    justify-content: center;
    gap: 22px;
  }
  .brand-dot {
    width: 96px; height: 96px;
    border-radius: 50%;
    background: #ffffff;
  }
  .brand-name {
    font-family: "Roboto Condensed", sans-serif;
    font-weight: 700;
    font-size: 70px;
    color: #ffffff;
    letter-spacing: 1px;
  }
</style>
</head>
<body>

<section class="card card-front">
  <h1 class="holder-name">Marla Quint</h1>
  <p class="holder-title">OWNER</p>

  <div class="contact-row">
    <span class="contact-item">
      <svg viewBox="0 0 16 16"><rect x="4" y="1.5" width="8" height="13" rx="1.5"/><circle class="solid" cx="8" cy="12.3" r="0.9"/></svg>
      555-218-4603
    </span>
    <span class="contact-item">
      <svg viewBox="0 0 16 16"><path class="solid" d="M1 6 Q8 1 15 6 L13 8 L11 6.5 L11 5 Q8 4 5 5 L5 6.5 L3 8 Z"/><path class="solid" d="M4 9 L12 9 L14 14 L2 14 Z"/></svg>
      555-647-1925
    </span>
    <span class="contact-item">
      <svg viewBox="0 0 16 16"><rect class="solid" x="1.5" y="3.5" width="13" height="9" rx="1"/><path d="M2 4.5 L8 9 L14 4.5" stroke="#fff"/></svg>
      Marla@TumbleTrips.example
    </span>
    <span class="contact-item">
      <svg viewBox="0 0 16 16"><circle cx="8" cy="8" r="6.3"/><ellipse cx="8" cy="8" rx="2.8" ry="6.3"/><path d="M1.7 8 H14.3 M2.8 4.8 H13.2 M2.8 11.2 H13.2"/></svg>
      www.TumbleTrips.example
    </span>
  </div>

  <div class="rule"></div>

  <div class="specialties">
    <span class="specialty">
      <svg viewBox="0 0 10 10"><path d="M5 0 L6 4 L10 5 L6 6 L5 10 L4 6 L0 5 L4 4 Z" fill="#3a8fd0"/></svg>
      Glimmerland destinations
    </span>
    <span class="specialty">
      <svg viewBox="0 0 10 10"><path d="M5 0 L6 4 L10 5 L6 6 L5 10 L4 6 L0 5 L4 4 Z" fill="#8cbf3f"/></svg>
      Pelican Bay Fun Park
    </span>
    <span class="specialty">
      <svg viewBox="0 0 10 10"><path d="M5 0 L6 4 L10 5 L6 6 L5 10 L4 6 L0 5 L4 4 Z" fill="#e2702a"/></svg>
      Cruises and All-Inclusive Vacations
    </span>
  </div>
</section>

<section class="card card-back">
  <div class="brand">
    <span class="brand-dot"></span>
    <span class="brand-name">TumbleTrips</span>
  </div>
</section>

</body>
</html>
```